Business Card Design for Training Business

Clear Path Coaching is a new business that delivers training and other services with a focus on topics related to mental health and wellbeing, for example, Wellmind Response Course, Resilience etc. We have a strong focus on evidence-based psychology and neuroscience. I have a logo which I will upload with the brief, so please consider colours that work well with the logo.
Target Market(s)
Adults, workplaces (particularly government and not-for-profits)
Industry/Entity Type
Business
Contact Information for Business Card
Head Strong TrainingSamantha SellwoodDirector0438 770 850sam@headstrongtraining.com.auwww.headstrongtraining.com.au

```html
<!DOCTYPE html>
<html lang="en">
<head>
<meta charset="utf-8">
<title>Clear Path Coaching – Business Card</title>
<link href="https://fonts.googleapis.com/css2?family=Questrial&display=swap" rel="stylesheet">
<style>
  :root {
    --teal: #22b8bd;
    --teal-deep: #1eaeb3;
    --paper: #f8f8f8;
    --ink: #4a4a4a;
    --ink-soft: #5a5a5a;
    --backdrop: #3b3b3b;
    --white: #ffffff;
  }
  * { margin: 0; padding: 0; box-sizing: border-box; }
  html, body {
    width: 1200px; height: 750px; overflow: hidden;
    background: var(--backdrop);
    font-family: "Questrial", "Century Gothic", sans-serif;
  }
  .stage { position: relative; width: 1200px; height: 750px; }
  .card {
    position: absolute; left: 371px; width: 461px; height: 262px;
    border-radius: 12px; overflow: hidden;
  }
  .card--front { top: 106px; background: var(--paper); }
  .card--back { top: 387px; background: var(--teal); }

  .side-band {
    position: absolute; left: 30px; top: 0; width: 70px; height: 100%;
    background: var(--teal);
  }
  .brand-dot {
    position: absolute; left: 28px; top: 28px; width: 74px; height: 74px;
    border-radius: 50%; background: var(--white);
    border: 3px solid var(--teal-deep);
  }
  .brand-name {
    position: absolute; left: 112px; top: 46px; width: 190px;
    color: var(--ink); text-align: center; font-weight: 400;
  }
  .brand-name__main { display: block; font-size: 20px; letter-spacing: 2.5px; }
  .brand-name__sub { display: block; font-size: 10px; letter-spacing: 4px; margin-top: 4px; }

  .person { position: absolute; left: 111px; top: 144px; }
  .person__name { color: var(--teal); font-size: 19px; letter-spacing: 0.3px; }
  .person__role { color: var(--ink); font-size: 13.5px; margin-top: 1px; }

  .contact { position: absolute; left: 111px; top: 194px; list-style: none; }
  .contact li { color: var(--ink-soft); font-size: 11.8px; height: 17.6px; line-height: 17.6px; }

  .icon { position: absolute; left: 55px; fill: var(--white); }
  .icon--person { top: 150px; }
  .icon--phone { top: 197px; }
  .icon--mail { top: 216px; }
  .icon--web { top: 233px; }

  .back-mark {
    position: absolute; left: 0; top: 62px; width: 100%; text-align: center;
    color: var(--white);
  }
  .back-mark__dot {
    display: block; margin: 0 auto 12px; width: 40px; height: 40px;
    border-radius: 50%; border: 2px solid var(--white);
  }
  .back-mark__name { display: block; font-size: 20px; letter-spacing: 3px; }
  .back-url {
    position: absolute; left: 0; top: 226px; width: 100%; text-align: center;
    color: var(--white); font-size: 12.5px;
  }
</style>
</head>
<body>
<main class="stage">
  <section class="card card--front" aria-label="Card front">
    <div class="side-band"></div>
    <div class="brand-dot"></div>
    <h1 class="brand-name">
      <span class="brand-name__main">CLEAR PATH</span>
      <span class="brand-name__sub">COACHING</span>
    </h1>

    <svg class="icon icon--person" width="18" height="18" viewBox="0 0 18 18" aria-hidden="true">
      <circle cx="9" cy="5" r="4"/>
      <path d="M1 18c0-5 3.5-7 8-7s8 2 8 7z"/>
    </svg>
    <svg class="icon icon--phone" width="12" height="12" viewBox="0 0 12 12" aria-hidden="true">
      <path d="M2.5 0.5l2 2.6-1.2 1.3c.7 1.6 1.8 2.8 3.4 3.6l1.3-1.2 2.6 2-1.1 2.4C4.8 11 1 7 0.3 1.6z"/>
    </svg>
    <svg class="icon icon--mail" width="12" height="9" viewBox="0 0 12 9" aria-hidden="true">
      <path d="M0 0h12v1.2L6 5 0 1.2z"/>
      <path d="M0 2.6l6 3.8 6-3.8V9H0z"/>
    </svg>
    <svg class="icon icon--web" width="12" height="12" viewBox="0 0 12 12" aria-hidden="true">
      <circle cx="6" cy="6" r="6"/>
      <path d="M3 3.5c1.2-.3 2 .4 2.2 1.4.2 1-.8 1.6-1.5 2.2L3 9c-1-.9-1.5-2.4-1.2-3.8z" fill="var(--teal)"/>
      <path d="M7.5 2c1 .2 2 .9 2.5 1.8-.8.4-1.7.2-2.3-.4z" fill="var(--teal)"/>
    </svg>

    <div class="person">
      <p class="person__name">Rebecca Tanfield</p>
      <p class="person__role">Director</p>
    </div>
    <ul class="contact">
      <li>0491 362 517</li>
      <li>bec@clearpathcoaching.example.au</li>
      <li>www.clearpathcoaching.example.au</li>
    </ul>
  </section>

  <section class="card card--back" aria-label="Card back">
    <div class="back-mark">
      <span class="back-mark__dot"></span>
      <span class="back-mark__name">CLEAR PATH COACHING</span>
    </div>
    <p class="back-url">www.clearpathcoaching.example.au</p>
  </section>
</main>
</body>
</html>
```